Automotive eCommerce Business looking for a business card design

Looking for a clean and simple business card design. Our company name is "Brindle Auto" and we are a company specializing in the ecommerce sales of automotive parts, specifically for pick up trucks and large SUVs. Our company colours are red, black, and white.

Feel free to use the logo provided or create a new logo that you seem fit. Looking forward to your creative ideas!

Industry/Entity Type

Automotive

Contact Information for Business Card

We were thinking of a possibly two-sided design featuring just the logo and company name on one side, and personal information on the other side. Single sided designs will be considered as well.

Font styles to use
Serif
Sans Serif
Decorative

Colors
ec1f27
ffffff
000000

Requirements
Must have
• Space for employee's name, title, phone number and email address, along with the company address and website somewhere.

```html
<!DOCTYPE html>
<html lang="en">
<head>
<meta charset="UTF-8">
<title>Brindle Auto – Business Card</title>
<link rel="stylesheet" href="https://fonts.googleapis.com/css2?family=Roboto:wght@400;500;700&display=swap">
<style>
  :root {
    --page-bg: #d9d3cc;
    --red-deep: #6e0f16;
    --red-main: #8f2229;
    --red-soft: #a8454a;
    --black: #141213;
    --charcoal: #2a2627;
    --white: #ffffff;
    --text-light: #f1e4e4;
    --frost: rgba(255, 255, 255, 0.72);
    --frost-edge: rgba(255, 255, 255, 0.9);
    --logo-ink: #1a1617;
  }
  * { margin: 0; padding: 0; box-sizing: border-box; }
  html, body {
    width: 1200px;
    height: 969px;
    overflow: hidden;
    background: var(--page-bg);
    font-family: "Roboto", Arial, sans-serif;
  }
  .canvas {
    position: relative;
    width: 1200px;
    height: 969px;
  }
  .card {
    position: absolute;
    left: 100px;
    top: 200px;
    width: 1000px;
    height: 570px;
    border-radius: 22px;
    overflow: hidden;
    background: linear-gradient(90deg, var(--red-main) 0%, var(--red-deep) 45%, var(--charcoal) 78%, var(--black) 100%);
    box-shadow: 0 18px 40px rgba(0, 0, 0, 0.25);
  }
  .card::before {
    content: "";
    position: absolute;
    inset: 0;
    background: radial-gradient(ellipse at 20% 60%, rgba(168, 69, 74, 0.55), transparent 60%);
  }
  .frost-panel {
    position: absolute;
    left: 395px;
    top: 36px;
    width: 575px;
    height: 500px;
    border-radius: 60px;
    background: linear-gradient(160deg, var(--frost-edge) 0%, var(--frost) 55%, rgba(255, 255, 255, 0.6) 100%);
    border: 2px solid rgba(255, 255, 255, 0.85);
  }
  .person {
    position: absolute;
    left: 55px;
    top: 68px;
    color: var(--white);
  }
  .person-name {
    font-size: 29px;
    font-weight: 500;
    letter-spacing: 0.5px;
  }
  .person-title {
    margin-top: 8px;
    font-size: 22px;
    font-weight: 400;
    color: var(--text-light);
  }
  .address {
    position: absolute;
    left: 55px;
    top: 270px;
    font-size: 22px;
    line-height: 32px;
    color: var(--text-light);
  }
  .contacts {
    position: absolute;
    left: 55px;
    top: 352px;
    list-style: none;
    font-size: 22px;
    color: var(--text-light);
  }
  .contacts li {
    display: flex;
    align-items: center;
    height: 32px;
  }
  .contacts svg {
    width: 20px;
    height: 20px;
    margin-right: 16px;
    fill: var(--text-light);
  }
  .brand-name {
    position: absolute;
    left: 395px;
    top: 260px;
    width: 575px;
    text-align: center;
    font-size: 40px;
    font-weight: 500;
    letter-spacing: 2px;
    color: var(--logo-ink);
  }
</style>
</head>
<body>
<div class="canvas">
  <div class="card">
    <div class="frost-panel"></div>

    <div class="person">
      <div class="person-name">OWEN HARTLEY</div>
      <div class="person-title">CEO/FOUNDER</div>
    </div>

    <div class="address">
      2140 Larkspur Road<br>
      Fairbanks, Alaska 99701
    </div>

    <ul class="contacts">
      <li>
        <svg viewBox="0 0 24 24"><path d="M6.6 10.8a15.1 15.1 0 0 0 6.6 6.6l2.2-2.2c.3-.3.7-.4 1-.2 1.1.4 2.3.6 3.6.6.6 0 1 .4 1 1V20c0 .6-.4 1-1 1A17 17 0 0 1 3 4c0-.6.4-1 1-1h3.5c.6 0 1 .4 1 1 0 1.3.2 2.5.6 3.6.1.3 0 .7-.2 1l-2.3 2.2z"/></svg>
        907 555 0148
      </li>
      <li>
        <svg viewBox="0 0 24 24"><path d="M7 1h10a2 2 0 0 1 2 2v18a2 2 0 0 1-2 2H7a2 2 0 0 1-2-2V3a2 2 0 0 1 2-2zm0 3v14h10V4H7zm5 15.5a1 1 0 1 0 0 2 1 1 0 0 0 0-2z"/></svg>
        907 555 0172
      </li>
      <li>
        <svg viewBox="0 0 24 24"><path d="M6 2h9l3 3v4h1a3 3 0 0 1 3 3v7h-4v3H6v-3H2v-7a3 3 0 0 1 3-3h1V2zm2 2v5h8V6h-2V4H8zm0 12v4h8v-4H8z"/></svg>
        907 555 0196
      </li>
      <li>
        <svg viewBox="0 0 24 24"><path d="M3 5h18a1 1 0 0 1 1 1v12a1 1 0 0 1-1 1H3a1 1 0 0 1-1-1V6a1 1 0 0 1 1-1zm1 2.2V17h16V7.2l-8 5.3-8-5.3zM5.5 7l6.5 4.3L18.5 7h-13z"/></svg>
        owen@brindleauto.com
      </li>
      <li>
        <svg viewBox="0 0 24 24"><path d="M12 2a10 10 0 1 0 0 20 10 10 0 0 0 0-20zm-1 17.9A8 8 0 0 1 4.2 10L9 14.8v1a2 2 0 0 0 2 2v2.1zm6.9-2.6A2 2 0 0 0 16 16h-1v-3a1 1 0 0 0-1-1H8v-2h2a1 1 0 0 0 1-1V7h2a2 2 0 0 0 2-2v-.4a8 8 0 0 1 2.9 12.7z"/></svg>
        www.brindleauto.com
      </li>
    </ul>

    <div class="brand-name">BRINDLE AUTO LTD.</div>
  </div>
</div>
</body>
</html>
```